Internal Office Slogans / Motto / Vision Statements

Hi. We would like to put up some posters around the office with quotations such as -
-”Do what you do so well that they will want to see it again and bring their friends.”- Hollis Brandt
-Make your customers feel heard and understood. Make your customers feel respected and liked. Make your customers feel appreciated and helped. Understand that you can do none of these things unless you are sincere about them.
Terrence Oakley
- It’s a very predictable and satisfying phenomenon: whenever we get better, our customers do too.
Cal Pruett
-Catch people in the act of performing extraordinary customer service. Treat them like heroes. Tell their stories, far and wide.
Ned Farraday

The purpose of the posters is to reiterate our culture and vision within the organisation. They should be clean, crisp and eye catching, not gaudy or bright. Professional, bold and strong.

The company website and logo is at http://www.nexoraweb.com.au
Print size will be A1

Thanks for participating & looking forward to seeing your great work.
Updates

Hi All. . 

So to reiterate we are looking for one background design to be used for multiple quotes...  The list of quotes are as follows: 

Support and or Sales Office

 

Make your customers feel heard and understood.Make your customers feel respected and liked. Make your customers feelappreciated and helped. Understand that you can do none of these things unlessyou are sincere about them.

Terrence Oakley

 

Nothing liberates our greatness like the desireto help, the desire to serve

Dorothea Quill

 

It’s a very predictable and satisfying phenomenon:whenever we get better, our customers do too.

Cal Pruett

 

Success means we go to sleep at night knowingthat our talents and abilities were used in a way that served others.

Dorothea Quill.

 

The sole purpose of business is to create, serveand satisfy a customer, from beginning to end – and that’s everyone’s job.

Ned Farraday

 

We don’t celebrate closing a sale, we celebrateopening a relationship.

Rosalind Hext

I will never make you a promise – unless I giveyou a plan and procedure to make that promise possible.

Bo Tennant

 

Customers feel we take them for granted; onlyshow interest when we want an order; lavish our time on prospects; communicatemainly by invoice; are fixated on big accounts; drop them like hot potatoesonce we have the order; don’t follow through on promises; and satisfy our ownbureaucracy rather than their needs. We can do better than that, much better.

Alan P Merrow.

 

 

General and public area

 

Catch people in the act of performingextraordinary customer service. Treat them like heroes. Tell their stories, farand wide.

Ned Farraday

 

 

We see our customers as invited guests to aparty, and we are the hosts. It’s our job every day to make every importantaspect of the customer experience a little bit better." Carl Voight - Founder andCEO of Halverin

 

"If you do build a great experience,customers tell each other about that. Word of mouth is verypowerful."  Carl Voight

 

It's not a faithin technology. It's faith in people. Rick Palmer

 

“Being the richest man in the cemetery doesn’tmatter to me … Going to bed at night saying we’ve done something wonderful…that’s what matters to me.” Rick Palmer

 

The customer experience is the next competitivebattleground. Lance Morrow, CIO, Vantor Computers

 

”Do what you do so well that they will want tosee it again and bring their friends.”- Hollis Brandt

In the world of internet customer service, it isimportant to remember your competitor is only a mouse click away. FrankHolden (not sure who he is but like the quote).

The customer is why you go to work. If they goaway, you do, too. Peter Lindqvist (?)

 

MaybeSome for Sales or Build Team:

Quality is remembered long after the price is forgotten. Marzetti Family Slogan

```html
<!DOCTYPE html>
<html lang="en">
<head>
<meta charset="utf-8">
<title>Customer Service Quote Poster</title>
<link rel="stylesheet" href="https://fonts.googleapis.com/css2?family=Anton&family=Questrial&display=swap">
<style>
  :root {
    --paper-light: #f3e3c2;
    --paper-mid: #e6cf9f;
    --paper-edge: #c9a46a;
    --frame-ink: #3b3a38;
    --hole: #111111;
    --quote-fill: #ffffff;
    --quote-outline: #141414;
    --author: #b5461b;
  }
  html, body {
    margin: 0;
    padding: 0;
    width: 848px;
    height: 1200px;
    overflow: hidden;
    background: #ffffff;
  }
  .poster {
    position: relative;
    width: 848px;
    height: 1200px;
    overflow: hidden;
  }
  .poster__paper {
    position: absolute;
    inset: 0;
    background:
      radial-gradient(ellipse at 45% 40%, var(--paper-light) 0%, var(--paper-mid) 60%, var(--paper-edge) 100%);
  }
  .poster__frame {
    position: absolute;
    inset: 0;
  }
  .poster__hole {
    position: absolute;
    left: 10px;
    width: 22px;
    height: 22px;
    border-radius: 50%;
    background: var(--hole);
  }
  .poster__quote {
    position: absolute;
    left: 140px;
    top: 255px;
    width: 590px;
    margin: 0;
    text-align: center;
    font-family: "Anton", "Impact", sans-serif;
    font-size: 43px;
    line-height: 61.5px;
    letter-spacing: 2px;
    color: var(--quote-fill);
    -webkit-text-stroke: 7px var(--quote-outline);
    paint-order: stroke fill;
  }
  .poster__author {
    position: absolute;
    left: 432px;
    top: 972px;
    margin: 0;
    font-family: "Questrial", sans-serif;
    font-size: 27px;
    font-weight: 700;
    letter-spacing: 1px;
    line-height: 1;
    color: var(--author);
    transform: rotate(8deg);
    transform-origin: left top;
    white-space: nowrap;
  }
</style>
</head>
<body>
<main class="poster">
  <div class="poster__paper" role="img" aria-label="Aged, stained paper texture background"></div>

  <svg class="poster__frame" width="848" height="1200" viewBox="0 0 848 1200" aria-hidden="true">
    <g fill="none" stroke="var(--frame-ink)" stroke-linecap="round" stroke-linejoin="round">
      <polygon points="160,120 830,236 706,1060 22,966" stroke-width="7"/>
      <polygon points="166,129 820,240 700,1050 30,958" stroke-width="3"/>
      <polyline points="150,128 560,196" stroke-width="4"/>
      <polyline points="818,250 742,760" stroke-width="3"/>
      <polyline points="18,950 420,1012" stroke-width="4"/>
      <polyline points="154,140 40,900" stroke-width="3"/>
    </g>
  </svg>

  <span class="poster__hole" style="top:96px"></span>
  <span class="poster__hole" style="top:422px"></span>
  <span class="poster__hole" style="top:752px"></span>
  <span class="poster__hole" style="top:1081px"></span>

  <p class="poster__quote">
    Make your customers feel<br>
    heard and<br>
    understood.Make your<br>
    customers feel respected<br>
    and liked. Make your<br>
    customers feel<br>
    appreciated and helped.<br>
    Understand that you can<br>
    do none of these things<br>
    unlessyou are sincere<br>
    about them.
  </p>

  <p class="poster__author">Terrence Oakley</p>
</main>
</body>
</html>
```